Need Business Card for our Real Estate Business with Sales Executive's Picture

PANTONE 484 C ( RED)

PANTONE 2766 C ( BLUE

Industry/Entity Type

Real Estate

Contact Information for Business Card

Name, Mobile, email, & picture of Person
Agency Phone, address, Web address

Requirements
Must have
• Our Logo Colours, Agent Picture,

```html
<!DOCTYPE html>
<html lang="en">
<head>
<meta charset="utf-8">
<title>Aldera Real Estate – Business Card</title>
<link rel="stylesheet" href="https://fonts.googleapis.com/css2?family=Amaranth:wght@700&family=Open+Sans:wght@400;600&display=swap">
<style>
  :root {
    --brand-red: #9a3324;
    --brand-blue: #141b4d;
    --card-white: #fbfbfb;
    --page-bg: #e9e9ec;
    --contact-text: #f6e3df;
  }
  * { box-sizing: border-box; margin: 0; padding: 0; }
  html, body {
    width: 1200px; height: 1054px; overflow: hidden;
    background: var(--page-bg);
  }
  .card {
    position: absolute; left: 80px; top: 214px;
    width: 1040px; height: 626px;
    background: var(--card-white);
    overflow: hidden;
    box-shadow: 0 10px 30px rgba(0,0,0,.15);
    font-family: "Open Sans", sans-serif;
  }
  .card-waves { position: absolute; inset: 0; }
  .brand {
    position: absolute; left: 96px; top: 100px;
    display: flex; align-items: center; gap: 18px;
  }
  .brand-mark { width: 34px; height: 34px; background: var(--brand-blue); }
  .brand-name {
    font-family: "Open Sans", sans-serif; font-weight: 600;
    font-size: 40px; letter-spacing: 4px; color: var(--brand-blue);
    text-transform: uppercase;
  }
  .person {
    position: absolute; right: 53px; top: 76px; text-align: right;
  }
  .person-name {
    font-family: "Amaranth", sans-serif; font-weight: 700;
    font-size: 38px; color: var(--brand-blue); line-height: 1.1;
  }
  .person-title {
    font-size: 25px; color: var(--brand-red); line-height: 1.3;
  }
  .edge-dot {
    position: absolute; right: -38px; top: 76px;
    width: 80px; height: 80px; border-radius: 50%;
    background: var(--brand-red);
  }
  .portrait {
    position: absolute; left: 0; top: 225px; width: 395px; height: 401px;
    background: linear-gradient(180deg, #cdb7a6 0%, #b89884 45%, #2a3a6a 72%, #1c2654 100%);
    border-top-right-radius: 180px 200px;
  }
  .contact-list {
    position: absolute; right: 32px; top: 398px;
    list-style: none; text-align: right;
    color: var(--contact-text); font-size: 24px; line-height: 34.5px;
  }
  .contact-list li { display: flex; justify-content: flex-end; align-items: center; gap: 16px; }
  .contact-list svg { width: 22px; height: 22px; fill: none; stroke: var(--contact-text); stroke-width: 2; }
  .address {
    position: absolute; right: 53px; top: 545px;
    color: var(--contact-text); font-size: 24px;
  }
</style>
</head>
<body>
  <div class="card">
    <svg class="card-waves" viewBox="0 0 1040 626" aria-hidden="true">
      <path d="M0,432 C120,470 250,528 400,512 C600,486 800,322 1040,290 V626 H0Z" fill="var(--brand-red)"/>
      <path d="M0,380 C130,410 230,488 330,490 C560,480 800,300 1040,255 L1040,280 C800,326 570,504 330,512 C220,512 120,442 0,410Z" fill="var(--brand-blue)"/>
    </svg>

    <div class="brand">
      <span class="brand-mark"></span>
      <span class="brand-name">Aldera Real Estate</span>
    </div>

    <div class="person">
      <p class="person-name">Maren Holloway</p>
      <p class="person-title">Managing Director</p>
    </div>
    <span class="edge-dot"></span>

    <div class="portrait" role="img" aria-label="Portrait photo of the sales executive in a navy suit"></div>

    <ul class="contact-list">
      <li>555.210.4481
        <svg viewBox="0 0 24 24"><rect x="6" y="2" width="12" height="20" rx="2"/><line x1="10" y1="18" x2="14" y2="18"/></svg></li>
      <li>555-310-7726
        <svg viewBox="0 0 24 24"><path d="M5 3h4l2 5-3 2a12 12 0 0 0 6 6l2-3 5 2v4a2 2 0 0 1-2 2A17 17 0 0 1 3 5a2 2 0 0 1 2-2z"/></svg></li>
      <li>alderarealestate.com
        <svg viewBox="0 0 24 24"><circle cx="12" cy="12" r="9"/><path d="M3 12h18M12 3c3 3 3 15 0 18M12 3c-3 3-3 15 0 18"/></svg></li>
      <li>mholloway@alderarealestate.com
        <svg viewBox="0 0 24 24"><rect x="3" y="5" width="18" height="14" rx="1"/><path d="M3 6l9 7 9-7"/></svg></li>
    </ul>
    <p class="address">418 Ridgeline Ave #210, Fairmont, CO 80011</p>
  </div>
</body>
</html>
```